Wix Design for a Clothing Design Web Marketing Site

We need a Wix design and content (including any images and copy) for a clothing design web storefront, Sew To Suit (or sewtosuit). Rough ideas and content can be found at http://marenvoltis.wix.com/sewtosuit.

Sew To Suit is an innovative business concept that combines fashion and entertainment. The business model allows customers to actively participate in the creation of fashion designs/concepts , visualize the garment in the customer’s body in 3D, and buy the physical garment made specially to fit the customer.
The fashion consultant will be able to create the design based on client's desires and test various possibilities (size, fabric, cut, etc..) in front of the customer, using software Drapova (the software is a key component of this business model)
(when developing the website use images from Drapova)
After the design is created, the customer can choose to order the actual piece. The garment will be made according to the created design, the customer measurements.

Target Market(s)

Primarily women from 25 to 45, who are fashion enthusiasts and appreciate fit and exclusivity. They are hedonistic shoppers, who shop for entertainment.
Men (metrosexuals) who are fashion enthusiasts, also hedonistic shoppers.

Industry/Entity Type

Clothing

Font styles to use
Serif
Sans Serif

Requirements
Must have
• Must have a landing page (home) or section, that gives the consumer an idea of what Sew To Suit will do for them, an about page or section that tells about the company and product, a how it works page or section that describes how it works (http://marenvoltis.wix.com/sewtosuit#!services3/c192y), and page or section about pricing, and a page or section on how to contact us.
Nice to have
• Very modern and clean. The website must be based on the main picture of the studio in the example. If that studio is the store, what will the website look like?
• Colors yellow, grey and white. Use the zig zag in yellow and white. You can change the size of the lines. The zig zagi gives the modern and bold accent. Outfits in pictures must show nicely tailored garments.

```html
<!DOCTYPE html>
<html lang="en">
<head>
<meta charset="utf-8">
<title>Sew To Suit — About Our Company</title>
<link rel="stylesheet" href="https://fonts.googleapis.com/css2?family=Roboto+Slab:wght@300;400;700&family=Roboto+Condensed:wght@400&family=Open+Sans:wght@400;600&family=Gabriela&display=swap">
<style>
  :root {
    --yellow: #f5e83a;
    --yellow-deep: #efd93a;
    --ink: #1b1b1b;
    --charcoal: #232323;
    --nav-grey: #5e6271;
    --footer-dark: #1e1e1e;
    --footer-base: #111111;
    --muted: #8b8b8b;
    --text: #3a3a3a;
    --white: #ffffff;
  }
  * { box-sizing: border-box; margin: 0; padding: 0; }
  html, body { width: 961px; height: 1200px; overflow: hidden; }
  body { position: relative; background: var(--white); font-family: "Open Sans", sans-serif; }

  .site-header { position: absolute; left: 0; top: 0; width: 961px; height: 163px; }
  .header-band { position: absolute; inset: 0; }
  .brand { position: absolute; left: 30px; top: 28px; display: flex; align-items: center; gap: 14px; }
  .brand-mark { width: 96px; height: 96px; border-radius: 50%; background: var(--yellow-deep); border: 5px solid #e6e6e6; }
  .brand-name { font-family: "Roboto Slab", serif; font-weight: 700; font-size: 28px; color: var(--ink); letter-spacing: 1px; }
  .tagline { position: absolute; left: 452px; top: 38px; font-family: "Gabriela", serif; font-size: 38px; line-height: 44px; color: var(--white); }

  .main-nav { position: absolute; left: 0; top: 163px; width: 961px; height: 38px; background: var(--nav-grey); display: flex; }
  .main-nav a { font-family: "Roboto Condensed", sans-serif; font-size: 16px; color: var(--white); text-decoration: none; line-height: 38px; padding: 0 29px; }
  .main-nav a.is-active { background: var(--ink); }

  .page-banner { position: absolute; left: 0; top: 201px; width: 961px; height: 113px; background: linear-gradient(135deg, #262626, #1a1a1a 60%, #222); }
  .page-banner h1 { text-align: center; font-family: "Roboto Slab", serif; font-weight: 400; font-size: 28px; color: var(--yellow); line-height: 122px; }

  .side-pattern { position: absolute; left: 0; top: 314px; width: 961px; height: 648px; background: linear-gradient(90deg, var(--yellow-deep), #f7eb9a 50%, var(--yellow-deep)); }

  .content-panel { position: absolute; left: 27px; top: 314px; width: 900px; height: 658px; background: var(--white); }
  .intro-title { position: absolute; top: 24px; width: 100%; text-align: center; font-family: "Roboto Slab", serif; font-weight: 300; font-size: 24px; color: var(--ink); }
  .divider { position: absolute; left: 346px; top: 66px; }
  .intro-text { position: absolute; left: 60px; top: 116px; width: 780px; text-align: center; font-size: 12.5px; line-height: 18.5px; color: var(--text); }
  .team-photo { position: absolute; left: 303px; top: 213px; width: 293px; height: 194px; border: 1px solid #bbb; background: linear-gradient(160deg, #dfe4e8, #b9bcc0 55%, #8e8a88); }

  .feature-card { position: absolute; top: 455px; width: 433px; height: 187px; background: var(--charcoal); display: flex; }
  .feature-card.card-womens { left: 9px; }
  .feature-card.card-mens { left: 456px; }
  .feature-body { width: 292px; padding: 16px 12px; }
  .feature-body h2 { font-family: "Roboto Slab", serif; font-weight: 300; font-size: 19px; color: var(--yellow); margin-bottom: 8px; }
  .feature-body p { font-size: 11.5px; line-height: 18.4px; color: var(--white); }
  .feature-body a { display: inline-block; margin-top: 4px; font-size: 11.5px; font-weight: 600; color: var(--yellow); }
  .feature-image { width: 141px; height: 187px; background: var(--yellow-deep); }
  .feature-image.dress { background: linear-gradient(90deg, var(--yellow-deep) 20%, #1a1a1a 20%, #1a1a1a 80%, var(--yellow-deep) 80%); }
  .feature-image.suit { background: linear-gradient(90deg, var(--yellow-deep) 10%, #1e2a48 10%, #1e2a48 90%, var(--yellow-deep) 90%); }

  .site-footer { position: absolute; left: 0; top: 962px; width: 961px; height: 190px; background: var(--footer-dark); }
  .footer-col { position: absolute; top: 42px; }
  .footer-col h3 { font-family: "Roboto Condensed", sans-serif; font-weight: 400; font-size: 14px; color: var(--muted); margin-bottom: 8px; }
  .footer-col li { list-style: none; font-size: 11px; line-height: 18.5px; color: #e6e6e6; }
  .footer-col .highlight { color: var(--yellow); }
  .col-links { left: 58px; }
  .col-info { left: 237px; }
  .col-newsletter { left: 478px; }
  .email-field { display: block; width: 218px; height: 31px; border: 0; padding: 0 8px; font-family: "Roboto Condensed", sans-serif; font-size: 11px; color: #999; background: var(--white); margin: 4px 0 9px 2px; }
  .submit-btn { display: block; width: 87px; height: 31px; margin-left: 2px; border: 0; background: var(--yellow); font-family: "Roboto Condensed", sans-serif; font-size: 13px; color: var(--ink); }
  .footer-brand { position: absolute; left: 730px; top: 44px; width: 182px; display: flex; flex-direction: column; align-items: center; gap: 6px; }
  .footer-brand .brand-mark { width: 88px; height: 88px; border: 4px solid #666; background: #807b2a; }
  .footer-brand .brand-name { font-size: 20px; color: #bfb52c; }

  .copyright { position: absolute; left: 0; top: 1152px; width: 961px; height: 48px; background: var(--footer-base); text-align: center; line-height: 48px; font-size: 10.5px; color: #ddd; }
</style>
</head>
<body>
  <header class="site-header">
    <svg class="header-band" width="961" height="163" aria-hidden="true">
      <polygon points="445,0 961,0 961,163 375,163" fill="#252525"/>
    </svg>
    <div class="brand">
      <span class="brand-mark"></span>
      <span class="brand-name">SEW TO SUIT</span>
    </div>
    <p class="tagline">Clothes made specially for<br>You and designed by you</p>
  </header>

  <nav class="main-nav">
    <a href="#">Home</a>
    <a href="#" class="is-active">What is Sew To Suit?</a>
    <a href="#">How It Works?</a>
    <a href="#">Price</a>
    <a href="#">Contact Us</a>
  </nav>

  <section class="page-banner"><h1>About Our Company</h1></section>

  <div class="side-pattern" role="img" aria-label="Yellow and white zigzag background pattern"></div>

  <main class="content-panel">
    <h2 class="intro-title">What is Sew To Suit?</h2>
    <svg class="divider" width="208" height="22" aria-hidden="true">
      <line x1="0" y1="11" x2="90" y2="11" stroke="#333" stroke-dasharray="3,1"/>
      <polygon points="104,1 114,11 104,21 94,11" fill="#1b1b1b"/>
      <line x1="118" y1="11" x2="208" y2="11" stroke="#333" stroke-dasharray="3,1"/>
    </svg>
    <p class="intro-text">Sew To Suit is an innovative business concept that combines fashion and entertainment. Our services allow you to actively participate in the creation of fashion designs/concepts , visualize the garment in 3D, and buy the physical garment made specially to fit you.</p>
    <div class="team-photo" role="img" aria-label="Photo of three fashion consultants at a design studio desk with a computer"></div>

    <article class="feature-card card-womens">
      <div class="feature-body">
        <h2>Lorel ipsum dolor sit amet</h2>
        <p>Donec pulvinar nec orci vel fermentum. Donec venenatis varius tincidunt. Aliquam erat volutpat. Maecenas rhoncus venenatis venenatis. Morbi aliquam nibh eget libero blandit, ac placerat tellus tristique.</p>
        <a href="#">Read More</a>
      </div>
      <div class="feature-image dress" role="img" aria-label="Photo of a tailored black sleeveless dress"></div>
    </article>

    <article class="feature-card card-mens">
      <div class="feature-body">
        <h2>Lorel ipsum dolor sit amet</h2>
        <p>Donec pulvinar nec orci vel fermentum. Donec venenatis varius tincidunt. Aliquam erat volutpat. Maecenas rhoncus venenatis venenatis. Morbi aliquam nibh eget libero blandit, ac placerat tellus tristique.</p>
        <a href="#">Read More</a>
      </div>
      <div class="feature-image suit" role="img" aria-label="Photo of a navy tailored suit on a mannequin"></div>
    </article>
  </main>

  <footer class="site-footer">
    <div class="footer-col col-links">
      <h3>QUICK LINKS</h3>
      <ul>
        <li>Home</li>
        <li>What is Sew To Suit?</li>
        <li>How It Works?</li>
        <li>Price</li>
        <li>Contact Us</li>
      </ul>
    </div>
    <div class="footer-col col-info">
      <h3>COMPANY INFO</h3>
      <ul>
        <li>58 Linden Row,</li>
        <li>2nd Floor, Suite 12</li>
        <li>Fairhaven, CA</li>
        <li>USA</li>
        <li>Ph: <span class="highlight">555 0142 376</span></li>
        <li>Email: <span class="highlight">hello@sewtosuit.example</span></li>
      </ul>
    </div>
    <div class="footer-col col-newsletter">
      <h3>SUBSCRIBE NEWSLETTER</h3>
      <input class="email-field" type="text" placeholder="Type your email id">
      <button class="submit-btn" type="button">SUBMIT</button>
    </div>
    <div class="footer-brand">
      <span class="brand-mark"></span>
      <span class="brand-name">SEW TO SUIT</span>
    </div>
  </footer>

  <div class="copyright">© 2015, All Rights Reserved, Sew To Suit</div>
</body>
</html>
```